Falkrin homes and renovations business card design.

Would like some new card designs utilizing my new logo that look professional. I am open to different colors on the logo or utilize the same ones we have. I like the original concept but would like to see some fresh ideas and build on what we have already done.

Target Market(s)

Custom home building industry, Real estate sales, Renovation projects.

Industry/Entity Type

Home Builder

Contact Information for Business Card

Falkrin Homes and Renovations
2871 96th Avenue
Kestrel Ridge, Northland
T2R3W8
Home : 403- 718-4063 Cell: 403- 294-5170

My info is : Dax Falkrin, President and CEO
email: falkrinhomes@maildrop-example.net
Website: falkrinhomes-example.com
websit

Requirements
Must have
• Must Use my new logo design. I am open to different colors on the logo or utilize the same ones in the existing design. I can upload the original logo design if needed.

```html
<!DOCTYPE html>
<html lang="en">
<head>
<meta charset="utf-8">
<title>Falkrin Homes and Renovations – Business Card</title>
<link rel="stylesheet" href="https://fonts.googleapis.com/css2?family=Montserrat:wght@400;500;600&display=swap">
<style>
  :root {
    --gold: #b5883a;
    --yellow: #f3b81f;
    --white: #ffffff;
    --grey: #6f6f6f;
    --stage: #2b2b2b;
  }
  * { box-sizing: border-box; margin: 0; padding: 0; }
  html, body { width: 1200px; height: 864px; overflow: hidden; }
  body {
    background: var(--stage);
    font-family: "Montserrat", sans-serif;
    position: relative;
  }
  .card {
    position: absolute;
    width: 630px;
    height: 360px;
    overflow: hidden;
  }
  .card-front { left: 70px; top: 50px; background: var(--gold); }
  .card-back { left: 500px; top: 454px; background: var(--white); }

  .front-brand {
    position: absolute; left: 0; right: 0; top: 130px;
    text-align: center; color: var(--white);
  }
  .brand-mark {
    display: inline-block; width: 14px; height: 14px;
    background: currentColor; margin-bottom: 10px;
  }
  .brand-name {
    font-weight: 600; font-size: 46px; letter-spacing: 2px;
    line-height: 1; text-transform: uppercase;
  }
  .brand-sub {
    font-weight: 600; font-size: 15px; letter-spacing: 2px;
    text-transform: uppercase; margin-top: 6px;
  }
  .front-web {
    position: absolute; left: 0; right: 0; top: 270px;
    text-align: center; color: var(--white); font-size: 15px;
  }

  .back-brand {
    position: absolute; right: 40px; top: 36px;
    text-align: right; color: var(--gold);
  }
  .back-brand .brand-name { font-size: 40px; }
  .back-brand .brand-sub { font-size: 12px; }

  .divider { position: absolute; height: 1px; background: var(--gold); }
  .divider-long { left: 215px; right: 40px; top: 180px; }
  .divider-short { left: 40px; width: 165px; top: 206px; }

  .person { position: absolute; left: 40px; top: 140px; }
  .person-name { color: var(--gold); font-weight: 600; font-size: 22px; }
  .person-title { color: var(--grey); font-size: 15px; margin-top: 2px; }

  .contacts {
    position: absolute; left: 40px; top: 220px;
    list-style: none; color: var(--grey); font-size: 15px;
  }
  .contacts li { display: flex; align-items: center; gap: 10px; height: 22px; }
  .contacts svg { width: 14px; height: 14px; fill: var(--yellow); }

  .address {
    position: absolute; right: 40px; top: 196px;
    text-align: right; color: var(--grey); font-size: 15px; line-height: 1.4;
  }
  .back-band { position: absolute; left: 0; top: 0; }
  .back-web {
    position: absolute; right: 40px; top: 316px;
    color: var(--white); font-size: 15px;
  }
</style>
</head>
<body>
  <section class="card card-front">
    <div class="front-brand">
      <span class="brand-mark"></span>
      <div class="brand-name">Falkrin</div>
      <div class="brand-sub">Homes and Renovations</div>
    </div>
    <p class="front-web">www.falkrinhomes-example.com</p>
  </section>

  <section class="card card-back">
    <div class="back-brand">
      <div class="brand-name">Falkrin</div>
      <div class="brand-sub">Homes and Renovations</div>
    </div>

    <div class="person">
      <p class="person-name">Dax Falkrin</p>
      <p class="person-title">President and CEO</p>
    </div>
    <div class="divider divider-long"></div>
    <div class="divider divider-short"></div>

    <ul class="contacts">
      <li><svg viewBox="0 0 16 16"><path d="M3 1l3 3-2 2c1 2 4 5 6 6l2-2 3 3-2 2C7 15 1 9 1 3z"/></svg>403- 718-4063</li>
      <li><svg viewBox="0 0 16 16"><path d="M4 0h8v16H4zM5.5 2v10h5V2z"/></svg>403- 294-5170</li>
      <li><svg viewBox="0 0 16 16"><path d="M0 3h16v10H0zM1 4l7 5 7-5z" fill-rule="evenodd"/></svg>falkrinhomes@maildrop-example.net</li>
    </ul>

    <p class="address">2871 96th Avenue<br>Kestrel Ridge, Northland, T2R3W8</p>

    <svg class="back-band" width="630" height="360" viewBox="0 0 630 360" aria-hidden="true">
      <path d="M0 334 L290 334 C318 334 322 294 352 292 L630 280 L630 286 L355 298 C328 300 322 340 292 340 L0 340 Z" fill="var(--yellow)"/>
      <path d="M0 346 L296 346 C326 346 330 302 360 300 L630 288 L630 360 L0 360 Z" fill="var(--gold)"/>
    </svg>
    <p class="back-web">falkrinhomes-example.com</p>
  </section>
</body>
</html>
```